Criação de Papelaria (6 itens) para Viagens & Lazer
A empresa queria:
" A Corvelo Viagens é uma marca Institucional que tem como propósito a realização de sonhos em todas as esferas do Negocio. "

```html
<!DOCTYPE html>
<html lang="pt-BR">
<head>
<meta charset="utf-8">
<title>Corvelo Viagens — Papelaria</title>
<link rel="stylesheet" href="https://fonts.googleapis.com/css2?family=Open+Sans:wght@300;400;600;700&display=swap">
<style>
:root{
  --bg:#ffffff;
  --ink:#6b6d70;
  --ink-dark:#4a4c4f;
  --ink-soft:#8c8e91;
  --accent:#d6177f;
  --social-a:#2f4f8f;
  --social-b:#2aa3dc;
  --social-c:#c9352b;
  --rainbow:linear-gradient(90deg,#e6007e 0%,#f39200 12%,#ffde00 22%,#95c11f 32%,#00a19a 42%,#009fe3 52%,#312783 62%,#8a1f82 72%,#e6007e 82%,#f39200 92%,#ffde00 100%);
}
*{box-sizing:border-box;margin:0;padding:0}
html,body{width:1200px;height:1200px;overflow:hidden;background:var(--bg)}
body{position:relative;font-family:"Open Sans",Arial,sans-serif;color:var(--ink)}

.rainbow-band{position:absolute;background:var(--rainbow)}

/* Banner */
.banner{position:absolute;left:79px;top:163px;width:1049px;height:245px;background:#fff;box-shadow:0 3px 10px rgba(0,0,0,.18)}
.banner .rainbow-band.top{left:0;top:0;width:100%;height:17px}
.banner .rainbow-band.bottom{left:0;bottom:0;width:100%;height:22px}
.photo{position:absolute}
.photo-ski{left:0;top:17px;width:233px;height:206px;background:linear-gradient(160deg,#cfe3f4 0%,#f2f6fa 45%,#e8edf2 70%,#f0f3f6 100%)}
.photo-ski::after{content:"";position:absolute;left:70px;top:40px;width:80px;height:110px;background:radial-gradient(ellipse at center,#e3501f 0%,rgba(227,80,31,.0) 70%)}
.logo-panel{position:absolute;left:233px;top:10px;width:319px;height:225px;background:#fff;box-shadow:0 2px 12px rgba(0,0,0,.25);display:flex;align-items:center;justify-content:center}
.photo-trip{left:552px;top:17px;width:497px;height:164px;background:linear-gradient(90deg,#d6c2ad 0%,#efd9c1 30%,#c9b6d9 60%,#a98dc6 80%,#e7d4e8 100%)}
.banner-contacts{position:absolute;left:552px;top:181px;width:497px;height:42px;display:flex;align-items:center;justify-content:flex-end;gap:30px;padding-right:26px;font-size:16px;color:var(--ink-dark)}
.banner-contacts .item{display:flex;align-items:center;gap:8px}

.brand{display:flex;align-items:center;gap:12px;color:var(--ink);font-weight:400;letter-spacing:.5px}
.brand .mark{display:block;background:var(--accent)}
.brand-sm{font-size:62px}
.brand-sm .mark{width:16px;height:16px}
.brand-lg{font-size:86px}
.brand-lg .mark{width:20px;height:20px}

/* Signature / card */
.sheet{position:absolute;left:79px;top:456px;width:1049px;height:619px;background:#fff;box-shadow:0 3px 10px rgba(0,0,0,.18)}
.sheet .rainbow-band.top{left:0;top:0;width:100%;height:31px}
.sheet .rainbow-band.bottom{left:0;bottom:0;width:100%;height:31px}
.sheet-header{position:absolute;left:0;top:55px;width:100%;height:142px;background:#fff;box-shadow:0 4px 10px rgba(0,0,0,.2);display:flex;align-items:center;justify-content:center}
.sheet-url{position:absolute;left:0;top:228px;width:100%;text-align:center;font-size:23px;color:var(--ink-soft)}

.col{position:absolute;top:286px}
.col-title{font-size:29px;font-weight:300;color:var(--ink);letter-spacing:.3px;white-space:nowrap}
.col-title b{font-weight:700}
.col-agencies{left:53px}
.col-contact{left:442px}
.col-social{left:792px}

.agency{display:flex;align-items:flex-start;gap:16px;margin-top:30px}
.flag{width:74px;height:48px;flex:none;margin-top:8px}
.flag-br{background:radial-gradient(circle at center,#2b49a0 0 12px,#f7d117 13px 22px,#1c9a47 23px)}
.flag-pe{background:linear-gradient(90deg,#d7192b 0 33%,#fff 33% 67%,#d7192b 67%)}
.agency-name{font-size:21px;font-weight:700;color:var(--ink-dark)}
.agency-addr{font-size:11px;line-height:15px;color:var(--ink-soft)}
.group-note{font-size:15px;color:var(--ink-soft);margin-top:16px;white-space:nowrap}
.group-note b{font-weight:700;color:var(--ink)}
.agency.second{margin-top:8px}

.contact{display:flex;gap:12px;margin-top:28px}
.contact + .contact{margin-top:16px}
.contact .icon{flex:none;margin-top:2px}
.contact-label{font-size:20px;font-weight:700;color:var(--ink-dark);line-height:24px}
.contact-line{font-size:21px;color:var(--ink);line-height:26px}
.contact-note{font-size:12px;color:var(--ink-soft);line-height:16px}

.social{display:flex;align-items:center;gap:14px;margin-top:28px;font-size:21px;color:var(--ink)}
.social + .social{margin-top:30px}
.dot{width:34px;height:34px;border-radius:50%;flex:none}
.dot-a{background:var(--social-a)}
.dot-b{background:var(--social-b)}
.dot-c{background:var(--social-c)}
</style>
</head>
<body>

<section class="banner">
  <div class="rainbow-band top" role="img" aria-label="Faixa de padrão geométrico colorido"></div>
  <div class="photo photo-ski" role="img" aria-label="Foto de esquiador descendo pista de neve"></div>
  <div class="photo photo-trip" role="img" aria-label="Fotos de destinos: pirâmides no deserto e dançarinos em trajes típicos"></div>
  <div class="logo-panel">
    <div class="brand brand-sm"><span class="mark"></span><span>Corvelo</span></div>
  </div>
  <div class="banner-contacts">
    <span class="item">
      <svg width="22" height="22" viewBox="0 0 24 24" aria-hidden="true"><circle cx="12" cy="12" r="10.5" fill="none" stroke="#6b6d70" stroke-width="1.5"/><path d="M8.6 7.2l1.6-.4 1 2.4-1 .8a6 6 0 0 0 3 3l.8-1 2.4 1-.4 1.6c-3.8.3-7.7-3.6-7.4-7.4z" fill="#6b6d70"/></svg>
      (11) 97420-5831
    </span>
    <span class="item">
      <svg width="22" height="22" viewBox="0 0 24 24" aria-hidden="true"><circle cx="12" cy="12" r="10.5" fill="none" stroke="#6b6d70" stroke-width="1.5"/><circle cx="12" cy="12" r="5.5" fill="none" stroke="#6b6d70" stroke-width="1.2"/><path d="M6.5 12h11M12 6.5c2 2 2 9 0 11M12 6.5c-2 2-2 9 0 11" fill="none" stroke="#6b6d70" stroke-width="1"/></svg>
      www.corvelo.com.br
    </span>
  </div>
  <div class="rainbow-band bottom" role="img" aria-label="Faixa de padrão geométrico colorido"></div>
</section>

<section class="sheet">
  <div class="rainbow-band top" role="img" aria-label="Faixa de padrão geométrico colorido"></div>
  <header class="sheet-header">
    <div class="brand brand-lg"><span class="mark"></span><span>Corvelo</span></div>
  </header>
  <p class="sheet-url">www.corvelo.com.br</p>

  <div class="col col-agencies">
    <h2 class="col-title"><b>NOSSAS</b> AGÊNCIAS</h2>
    <div class="agency">
      <div class="flag flag-br" role="img" aria-label="Bandeira do Brasil"></div>
      <div>
        <div class="agency-name">BRASIL</div>
        <div class="agency-addr">Rua das Acácias, 740 - Cj. 18<br>Vila Serena - São Paulo - SP</div>
      </div>
    </div>
    <p class="group-note">UMA EMPRESA DO <b>GRUPO CORVELO</b></p>
    <div class="agency second">
      <div class="flag flag-pe" role="img" aria-label="Bandeira do Peru"></div>
      <div>
        <div class="agency-name">PERU</div>
        <div class="agency-addr">Calle Los Andes, 412<br>Centro Histórico de Cusco</div>
      </div>
    </div>
  </div>

  <div class="col col-contact">
    <h2 class="col-title"><b>FALE</b> CONOSCO</h2>
    <div class="contact">
      <svg class="icon" width="30" height="30" viewBox="0 0 24 24" aria-hidden="true"><circle cx="12" cy="12" r="10.5" fill="none" stroke="#6b6d70" stroke-width="1.5"/><path d="M8.6 7.2l1.6-.4 1 2.4-1 .8a6 6 0 0 0 3 3l.8-1 2.4 1-.4 1.6c-3.8.3-7.7-3.6-7.4-7.4z" fill="#6b6d70"/></svg>
      <div>
        <div class="contact-label">Grande São Paulo</div>
        <div class="contact-line">+55 (11) 3046-7192</div>
        <div class="contact-label">Demais Regiões</div>
        <div class="contact-line">0800 041 3375</div>
      </div>
    </div>
    <div class="contact">
      <svg class="icon" width="30" height="30" viewBox="0 0 24 24" aria-hidden="true"><circle cx="12" cy="12" r="10.5" fill="none" stroke="#6b6d70" stroke-width="1.5"/><path d="M8.6 7.2l1.6-.4 1 2.4-1 .8a6 6 0 0 0 3 3l.8-1 2.4 1-.4 1.6c-3.8.3-7.7-3.6-7.4-7.4z" fill="#6b6d70"/></svg>
      <div>
        <div class="contact-label">Mensagens</div>
        <div class="contact-note">Somente Orçamentos</div>
        <div class="contact-line">(11) 9517-2684</div>
      </div>
    </div>
  </div>

  <div class="col col-social">
    <h2 class="col-title"><b>SIGA-</b>NOS</h2>
    <div class="social"><span class="dot dot-a"></span>mural</div>
    <div class="social"><span class="dot dot-b"></span>piado</div>
    <div class="social"><span class="dot dot-c"></span>círculo+</div>
  </div>

  <div class="rainbow-band bottom" role="img" aria-label="Faixa de padrão geométrico colorido"></div>
</section>

</body>
</html>
```